Outdoor Real Estate Sales Banner

It should say

248 Wexcombe Street, East Boston
Coming Spring 2026
3 Luxury Condos
Experience refined living with elegant design and high-end finishes. Thoughtfully crafted for both comfort and sophistication.
Construction by V Construction
Now Accepting Reservations

Schedule Your Private Tour Today
Marisol Thibault, Fenwick Realty | 617-555-0142 | Marisol@fenwickharbor.com
Gregory Hale, Fenwick Realty | 617-555-0187 | Gregory@fenwickharbor.com

Target Market(s)

30-45

Industry/Entity Type

real estate

Font styles to use
Serif

Requirements
Must have
• Colors of logo and preppy rich look
Nice to have
• herringbone incorporated the pattern
Should not have
• any loud colors

```html
<!DOCTYPE html>
<html lang="en">
<head>
<meta charset="utf-8">
<title>248 Wexcombe Street – Sales Banner</title>
<link rel="stylesheet" href="https://fonts.googleapis.com/css2?family=Lora:wght@400;500&family=Jost:wght@500&family=Poppins:wght@400;500;600&display=swap">
<style>
  :root {
    --navy: #2c3d5e;
    --navy-deep: #263654;
    --gold: #dfbb7c;
    --white: #ffffff;
    --siding: #e6d2a0;
    --siding-light: #efe0b8;
    --photo-warm: #c9b9a3;
    --photo-cool: #7f8a78;
  }
  * { margin: 0; padding: 0; box-sizing: border-box; }
  html, body { width: 1200px; height: 2400px; overflow: hidden; background: var(--navy); }
  .banner {
    position: relative; width: 1200px; height: 2400px; overflow: hidden;
    background: linear-gradient(180deg, var(--navy-deep), var(--navy) 50%, var(--navy-deep));
    font-family: "Lora", Georgia, serif;
  }
  .hero-shape { position: absolute; left: 0; top: 0; }
  .brand { position: absolute; left: 96px; top: 906px; width: 300px; text-align: center; color: var(--gold); font-family: "Lora", Georgia, serif; font-weight: 400; }
  .brand-mark { display: block; margin: 0 auto 14px; width: 122px; height: 122px; border: 4px solid var(--gold); border-radius: 50%; }
  .brand-name { font-size: 44px; line-height: 1; letter-spacing: 1px; }
  .brand-sub { font-size: 18px; letter-spacing: 12px; margin-top: 10px; padding-left: 12px; }
  .centered { position: absolute; left: 0; width: 1200px; text-align: center; line-height: 1; white-space: nowrap; }
  .address { top: 1172px; font-size: 94px; color: var(--gold); }
  .area { top: 1285px; font-family: "Jost", sans-serif; font-weight: 500; font-size: 52px; color: var(--white); }
  .rule { position: absolute; height: 2px; background: var(--gold); }
  .units { top: 1410px; font-size: 84px; color: var(--gold); }
  .timing { top: 1506px; font-family: "Poppins", sans-serif; font-weight: 500; font-size: 43px; color: var(--white); }
  .pitch { top: 1584px; font-family: "Poppins", sans-serif; font-size: 26.5px; line-height: 39px; color: var(--gold); white-space: normal; }
  .builder { top: 1706px; font-size: 38px; color: var(--white); }
  .call { top: 1824px; font-size: 54px; color: var(--gold); }
  .invite { top: 1908px; font-size: 53px; color: var(--white); }
  .agent { position: absolute; top: 2050px; display: flex; gap: 18px; }
  .agent-photo { width: 110px; height: 132px; }
  .agent-name { font-size: 40px; color: var(--gold); line-height: 1; margin-top: 0; }
  .agent-line { font-family: "Poppins", sans-serif; font-size: 21.5px; color: var(--white); line-height: 29.5px; }
  .agent-name + .agent-line { margin-top: 6px; }
  .agent-divider { position: absolute; left: 600px; top: 2060px; width: 2px; height: 112px; background: var(--gold); }
  .site { top: 2250px; font-family: "Poppins", sans-serif; font-weight: 600; font-size: 22px; letter-spacing: 7px; color: var(--white); }
</style>
</head>
<body>
<main class="banner">
  <svg class="hero-shape" width="1200" height="1220" viewBox="0 0 1200 1220" aria-hidden="false">
    <defs>
      <clipPath id="hero-clip"><circle cx="822" cy="466" r="673"/></clipPath>
      <linearGradient id="siding-tone" x1="0" y1="0" x2="1" y2="1">
        <stop offset="0" stop-color="var(--siding-light)"/>
        <stop offset="1" stop-color="var(--siding)"/>
      </linearGradient>
    </defs>
    <circle class="hero-ring" cx="807" cy="447" r="694" fill="var(--gold)"/>
    <circle class="hero-disc" cx="822" cy="466" r="673" fill="var(--white)"/>
    <g clip-path="url(#hero-clip)">
      <rect class="hero-elevation" x="358" y="0" width="842" height="1031" fill="url(#siding-tone)" role="img" aria-label="Architectural elevation rendering of the three-storey condominium building with cream clapboard siding, white-trimmed windows and a front entry stair"/>
    </g>
  </svg>

  <div class="brand">
    <span class="brand-mark"></span>
    <div class="brand-name">FENWICK</div>
    <div class="brand-sub">REALTY</div>
  </div>

  <h1 class="centered address" style="font-weight:400">248 Wexcombe Street</h1>
  <p class="centered area">East Boston</p>
  <div class="rule" style="left:216px; top:1372px; width:776px;"></div>

  <h2 class="centered units" style="font-weight:400">3 Luxury Condominiums</h2>
  <p class="centered timing">Coming Spring 2026</p>
  <p class="centered pitch">Experience refined living with elegant design and high-end finishes.<br>Thoughtfully crafted residences that balance comfort, sophistication,<br>and timeless New England character.</p>
  <p class="centered builder">Construction by V Construction</p>

  <div class="rule" style="left:210px; top:1794px; width:776px;"></div>
  <p class="centered call">NOW ACCEPTING RESERVATIONS</p>
  <div class="rule" style="left:210px; top:1891px; width:776px;"></div>
  <p class="centered invite">Schedule Your Private Tour Today</p>

  <div class="agent" style="left:67px;">
    <div class="agent-photo" role="img" aria-label="Portrait photo of agent Marisol Thibault" style="background:linear-gradient(160deg, var(--photo-warm), #8c7f72);"></div>
    <div>
      <div class="agent-name">Marisol Thibault</div>
      <div class="agent-line">Fenwick Realty</div>
      <div class="agent-line">617-555-0142</div>
      <div class="agent-line">Marisol@fenwickharbor.com</div>
    </div>
  </div>
  <div class="agent-divider"></div>
  <div class="agent" style="left:638px;">
    <div class="agent-photo" role="img" aria-label="Portrait photo of agent Gregory Hale" style="background:linear-gradient(160deg, var(--photo-cool), #3d4a66);"></div>
    <div>
      <div class="agent-name">Gregory Hale</div>
      <div class="agent-line">Fenwick Realty</div>
      <div class="agent-line">617-555-0187</div>
      <div class="agent-line">Gregory@fenwickharbor.com</div>
    </div>
  </div>

  <div class="rule" style="left:120px; top:2233px; width:959px;"></div>
  <p class="centered site">WWW.FENWICKHARBOR.COM</p>
</main>
</body>
</html>
```